Calvanto Group Real Estate Company business cards

New business card design, we are generally happy with the basic layout of the existing front of business card, (feel free to change) but require a head shot photo on the back side.

http://www.calvanto.com.au/

Attached logos, and existing business card

------------------------------

Target Market(s)

Real estate

Industry/Entity Type

Real Estate

Contact Information for Business Card

Standard size double sided

Font styles to use
Other font styles liked:
• Futura

Requirements
Must have
• Photo head shot on the back side
Nice to have
• yes
Should not have
• No

```html
<!DOCTYPE html>
<html lang="en">
<head>
<meta charset="utf-8">
<title>Calvanto Group – Business Card</title>
<link rel="stylesheet" href="https://fonts.googleapis.com/css2?family=Montserrat:wght@400;500;700&family=Roboto+Condensed:wght@700&display=swap">
<style>
  :root {
    --page-bg: #e9e7ee;
    --card-purple: #34206b;
    --card-purple-light: #3f2a7c;
    --text-white: #ffffff;
    --accent-orange: #f29a1f;
    --frame-white: #ffffff;
    --photo-light: #d9dbe0;
    --photo-dark: #2c3550;
  }
  * { box-sizing: border-box; margin: 0; padding: 0; }
  html, body { width: 1200px; height: 900px; overflow: hidden; }
  body {
    background: var(--page-bg);
    font-family: "Montserrat", Arial, sans-serif;
    color: var(--text-white);
    display: flex;
    flex-direction: column;
    align-items: center;
    justify-content: center;
    gap: 40px;
  }
  .card {
    position: relative;
    width: 700px;
    height: 400px;
    background: linear-gradient(135deg, var(--card-purple-light) 0%, var(--card-purple) 55%, var(--card-purple-light) 100%);
    box-shadow: 0 6px 18px rgba(30, 15, 60, 0.25);
    overflow: hidden;
  }

  /* Front side */
  .details {
    position: absolute;
    left: 70px;
    top: 52px;
  }
  .person {
    font-size: 23px;
    font-weight: 700;
    letter-spacing: 0.3px;
  }
  .person .role { font-weight: 400; }
  .company {
    margin-top: 30px;
    font-size: 19px;
    font-weight: 700;
    letter-spacing: 0.5px;
  }
  .abn {
    font-size: 15px;
    font-weight: 400;
    letter-spacing: 1px;
    margin-top: 2px;
  }
  .contact-list {
    list-style: none;
    margin-top: 30px;
    font-size: 17px;
    letter-spacing: 0.6px;
    line-height: 1.6;
  }
  .contact-list .label {
    color: var(--accent-orange);
    display: inline-block;
    width: 32px;
  }
  .contact-list .phone { font-weight: 700; font-size: 19px; letter-spacing: 1px; }
  .contact-list .web { margin-top: 14px; }
  .brand-vertical {
    position: absolute;
    right: -70px;
    top: 150px;
    transform: rotate(90deg);
    font-size: 52px;
    font-weight: 500;
    letter-spacing: 1px;
    color: var(--text-white);
  }

  /* Back side */
  .headshot-frame {
    position: absolute;
    left: 34px;
    top: 34px;
    width: 330px;
    height: 332px;
    border: 4px solid var(--frame-white);
    background: linear-gradient(180deg, var(--photo-light) 0%, var(--photo-light) 45%, var(--photo-dark) 100%);
  }
  .back-brand {
    position: absolute;
    left: 395px;
    top: 120px;
    width: 290px;
    text-align: center;
  }
  .brand-name {
    font-size: 54px;
    font-weight: 500;
    letter-spacing: 1px;
  }
  .services {
    margin-top: 30px;
    font-family: "Roboto Condensed", Arial, sans-serif;
    font-weight: 700;
    font-size: 32px;
    display: flex;
    justify-content: center;
    gap: 22px;
  }
  .services .divider { font-weight: 400; }
</style>
</head>
<body>
  <section class="card card-front" aria-label="Business card front">
    <div class="details">
      <p class="person">Daniel Tran <span class="role">| Director</span></p>
      <p class="company">Calvanto Group</p>
      <p class="abn">ABN: 12 345 678 901</p>
      <ul class="contact-list">
        <li><span class="label">M:</span><span class="phone">0400 555 123</span></li>
        <li><span class="label">E:</span>daniel.tran@calvanto.com.au</li>
        <li class="web"><span class="label">W:</span>www.calvanto.com.au</li>
      </ul>
    </div>
    <p class="brand-vertical">calvanto</p>
  </section>

  <section class="card card-back" aria-label="Business card back">
    <div class="headshot-frame" role="img" aria-label="Head shot photo of the director in a suit"></div>
    <div class="back-brand">
      <p class="brand-name">calvanto</p>
      <p class="services"><span>Buy</span><span class="divider">|</span><span>Sell</span><span class="divider">|</span><span>Rent</span></p>
    </div>
  </section>
</body>
</html>
```